Tessaline Air Business Card Design

Design new, 2 sides, business cards for a residential and light commercial heating, air conditioning contractor.

Target Market(s)

Homeowners, small businesses

Industry/Entity Type

Business

Contact Information for Business Card

Dominic Westerhall
Phone - 862-415-2736
Email
Address - PO box 518
Brightwater NJ 07912
Website - www.HarborBreezeLLC.example

Requirements
Must have
• logo, company colors, standard size with no die cut, so I can use nova stamp

```html
<!DOCTYPE html>
<html lang="en">
<head>
<meta charset="utf-8">
<title>Tessaline Air Business Cards</title>
<link rel="stylesheet" href="https://fonts.googleapis.com/css2?family=Roboto:wght@400;500;700&family=Roboto+Condensed:wght@700&display=swap">
<style>
  :root {
    --backdrop: #e4e4e4;
    --card: #f5f5f4;
    --card-shade: #ebebea;
    --maroon: #7b2434;
    --maroon-deep: #5e1a2a;
    --gold: #f0c75a;
    --rule: #e2b843;
    --orange: #d9801f;
    --red: #c33a20;
    --icon: #c6402a;
    --ink: #3a1c24;
    --white: #ffffff;
  }
  * { margin: 0; padding: 0; box-sizing: border-box; }
  html, body { width: 1200px; height: 576px; overflow: hidden; }
  body {
    background: var(--backdrop);
    position: relative;
    font-family: "Roboto", sans-serif;
  }
  .card {
    position: absolute;
    top: 138px;
    background: linear-gradient(180deg, var(--card) 0%, var(--card-shade) 100%);
    overflow: hidden;
  }
  .card--front { left: 81px; width: 485px; height: 294px; }
  .card--back { left: 602px; width: 481px; height: 292px; }

  .brand-name {
    position: absolute;
    font-family: "Roboto", sans-serif;
    font-weight: 700;
    color: var(--maroon);
    white-space: nowrap;
    transform: translate(-50%, -50%);
  }
  .card--front .brand-name { left: 243px; top: 130px; font-size: 40px; }
  .card--back .brand-name { left: 106px; top: 80px; font-size: 24px; }

  .service-band {
    position: absolute;
    left: 0; right: 0;
    top: 247px; height: 26px;
    background: var(--maroon);
    color: var(--gold);
    font-size: 12px;
    display: flex; align-items: center; justify-content: center;
    letter-spacing: 0.1px;
  }

  .person {
    position: absolute;
    right: 25px; top: 141px;
    text-align: right;
  }
  .person__name {
    font-family: "Roboto Condensed", sans-serif;
    font-weight: 700;
    font-size: 21px;
    color: var(--maroon-deep);
    line-height: 1;
  }
  .person__title {
    font-size: 10.5px;
    color: var(--ink);
    margin-top: 6px;
  }
  .divider {
    position: absolute;
    left: 25px; top: 177px;
    width: 336px; height: 1px;
    background: var(--rule);
  }
  .contacts {
    position: absolute;
    left: 28px; top: 200px;
    list-style: none;
  }
  .contacts li {
    display: flex; align-items: center;
    height: 18.5px;
    font-size: 12.5px;
    color: var(--ink);
  }
  .contacts svg { width: 12px; height: 12px; margin-right: 11px; fill: var(--icon); }

  .foot-orange {
    position: absolute;
    left: 0; top: 274px;
    width: 262px; height: 18px;
    background: var(--orange);
  }
  .foot-red {
    position: absolute;
    right: 0; top: 256px;
    width: 228px; height: 36px;
    background: var(--red);
    clip-path: polygon(14px 0, 100% 0, 100% 100%, 0 100%);
    color: var(--white);
    font-size: 12.5px;
    display: flex; align-items: center; justify-content: flex-end;
    padding-right: 24px;
  }
</style>
</head>
<body>

<section class="card card--front" aria-label="Business card front">
  <div class="brand-name">Tessaline Air</div>
  <div class="service-band">Residential &amp; Light Commercial Heating &nbsp;•&nbsp; Air Conditioning Contractor</div>
</section>

<section class="card card--back" aria-label="Business card back">
  <div class="brand-name">Tessaline Air</div>

  <div class="person">
    <div class="person__name">Dominic Westerhall</div>
    <div class="person__title">Managing Director</div>
  </div>
  <div class="divider"></div>

  <ul class="contacts">
    <li>
      <svg viewBox="0 0 24 24" aria-hidden="true"><path d="M3 6c0-2 3-3 9-3s9 1 9 3v2h-5V6.5c-1-.4-2.5-.5-4-.5s-3 .1-4 .5V8H3V6zm3 4h12l2 9H4l2-9zm6 2a3 3 0 1 0 0 6 3 3 0 0 0 0-6z"/></svg>
      862-415-2736
    </li>
    <li>
      <svg viewBox="0 0 24 24" aria-hidden="true"><path d="M2 5h20v14H2V5zm2 2v.5l8 5.5 8-5.5V7l-8 5.5L4 7zm0 3v7h16v-7l-8 5.5L4 10z"/></svg>
      info@TessalineAirLLC.example
    </li>
    <li>
      <svg viewBox="0 0 24 24" aria-hidden="true"><path d="M12 2a7 7 0 0 0-7 7c0 5 7 13 7 13s7-8 7-13a7 7 0 0 0-7-7zm0 4a3 3 0 1 1 0 6 3 3 0 0 1 0-6z"/></svg>
      PO box 518 Brightwater NJ 07912
    </li>
  </ul>

  <div class="foot-orange"></div>
  <div class="foot-red">TessalineAirLLC.example</div>
</section>

</body>
</html>
```